Executive Taxi firm with Chauffeur service Website

I have my domain name registered and I have started to work on my site but I am struggling. I am just about to get a logo for the company and need a web site that clearly represents the fact we are an executive/luxury brand in private hire vehicles. We offer airport transfers, train station transfers, seaport transfers, holiday transfers and business to business pick up and drop off.

Target Market(s)

Corporate people, holidaymakers looking for a luxury start their holiday. VIPs' and celebrities.

Number of Pages Required

5+ page

Font styles to use
Serif
Sans Serif
Decorative
Script

Colors

Designer to choose colors to be used in the design.

Requirements
Must have
• Home Page, Services, About Us, VIP and Contact us
• Please see www.brivomotors.co.uk I have started it but not happy with it at all.
Nice to have
• Booking form or enquiry form.

```html
<!DOCTYPE html>
<html lang="en">
<head>
<meta charset="utf-8">
<title>Brivo Motors – Private Hire, Chauffeur and Taxi Service</title>
<link href="https://fonts.googleapis.com/css2?family=Archivo:wght@700;800&family=Lato:wght@400;700;900&family=Michroma&display=swap" rel="stylesheet">
<style>
:root{
  --yellow:#ffe100;
  --yellow-deep:#ffc400;
  --ink:#1b1b1b;
  --dark:#262626;
  --navy:#2a3550;
  --grey:#6d6d6d;
  --line:#c9c9c9;
  --white:#ffffff;
}
*{box-sizing:border-box;margin:0;padding:0}
html,body{width:1200px;height:2970px;overflow:hidden}
body{position:relative;background:var(--white);font-family:'Lato',sans-serif;color:var(--ink)}
.abs{position:absolute}
.display{font-family:'Michroma',sans-serif}
.hero-photo{position:absolute;left:0;top:0;width:1200px;height:740px}
.site-name{left:186px;top:44px;font-family:'Lato',sans-serif;font-weight:900;font-size:30px;color:var(--yellow);letter-spacing:.5px;display:flex;align-items:center;gap:12px}
.site-name .mark{width:30px;height:30px;border-radius:50%;background:var(--yellow)}
.nav{top:34px;left:568px;display:flex;gap:0;font-size:15px;font-weight:700;color:var(--white)}
.nav a{color:inherit;text-decoration:none;padding:9px 14px;margin-right:14px;text-transform:uppercase}
.nav a.active{border:2px solid var(--white);padding:7px 22px}
.hero-kicker{left:186px;top:226px;font-family:'Archivo',sans-serif;font-weight:700;font-size:25px;color:var(--white)}
.hero-title{left:184px;top:264px;font-family:'Archivo',sans-serif;font-weight:800;font-size:48px;line-height:44px;color:var(--white)}
.btn{display:flex;align-items:center;justify-content:center;font-weight:900;text-transform:uppercase;font-size:16px}
.btn-yellow{background:var(--yellow);color:var(--ink)}
.btn-black{background:var(--ink);color:var(--white)}
.hero-btn{left:186px;top:422px;width:170px;height:48px;font-size:18px}
.dots{left:556px;top:640px;display:flex;gap:6px;align-items:center}
.dots span{width:8px;height:8px;border-radius:50%;background:rgba(255,255,255,.6)}
.dots .arrow{width:16px;height:16px;background:var(--white)}
.section-title{left:0;width:1200px;text-align:center;font-size:32px;color:var(--navy)}
.section-lead{left:220px;width:760px;text-align:center;font-size:19px;line-height:26px;color:var(--grey)}
.service{width:300px;height:300px;border-radius:50%;text-align:center;display:flex;flex-direction:column;align-items:center;padding-top:48px}
.service h3{font-family:'Archivo',sans-serif;font-size:17px;line-height:21px;margin-top:14px;text-transform:uppercase}
.service p{font-size:13.5px;line-height:16px;width:200px;margin-top:10px}
.service-dark{background:var(--dark);color:var(--white)}
.service-dark p{color:#a9a9a9}
.service-yellow{background:var(--yellow);color:var(--ink)}
.band{left:0;top:1250px}
.app-visual{left:170px;top:1310px;width:380px;height:490px}
.here-title{left:600px;top:1410px;font-size:32px;color:var(--ink)}
.here-copy{left:600px;top:1464px;width:460px;font-size:15.5px;line-height:22px;color:var(--ink)}
.here-copy p+p{margin-top:22px}
.here-btn{left:600px;top:1663px;width:150px;height:40px}
.vip-title{left:192px;top:1900px;font-size:34px;color:var(--ink)}
.vip-copy{left:196px;top:1956px;width:380px;font-size:16px;line-height:22px;color:var(--grey)}
.vip-copy p+p{margin-top:22px}
.vip-btn{left:192px;top:2130px;width:150px;height:40px}
.vip-accent{left:780px;top:1885px;width:238px;height:185px;background:var(--yellow)}
.vip-photo{left:582px;top:1902px;width:422px;height:286px}
.contact-bg{left:0;top:2260px}
.contact-title{left:178px;top:2436px;font-family:'Archivo',sans-serif;font-weight:800;font-size:28px;color:var(--white)}
.contact-copy{left:178px;top:2480px;width:240px;font-size:14px;line-height:19px;color:#d6d6d6}
.contact-line{left:174px;display:flex;align-items:center;gap:10px;color:var(--white);font-size:18px;font-weight:700}
.socials{display:flex;gap:6px}
.socials span{width:30px;height:30px;border-radius:50%;border:2px solid var(--yellow)}
.socials.dark span{width:33px;height:33px;border-color:var(--ink)}
.form-card{left:472px;top:2430px;width:546px;height:305px;background:var(--white)}
.form-title{position:absolute;left:34px;top:42px;font-family:'Archivo',sans-serif;font-weight:800;font-size:21px}
.field{position:absolute;width:232px;height:34px;border:1px solid var(--line);font-size:13px;color:#8a8a8a;padding:9px 10px;display:flex;align-items:center;gap:5px}
.form-btn{position:absolute;left:36px;top:225px;width:258px;height:38px}
.footer-nav{left:182px;top:2868px;display:flex;gap:30px;font-size:15px;font-weight:700;color:var(--ink)}
.copyright{left:182px;top:2902px;font-size:11px;color:var(--grey)}
</style>
</head>
<body>

<!-- Hero -->
<svg class="hero-photo" viewBox="0 0 1200 740" role="img" aria-label="Chauffeur opening the rear door of a black executive car for a businesswoman">
  <defs>
    <linearGradient id="heroGrad" x1="0" y1="0" x2="1" y2="1">
      <stop offset="0" stop-color="#4a5a3c"/>
      <stop offset=".45" stop-color="#2b2d2c"/>
      <stop offset="1" stop-color="#121314"/>
    </linearGradient>
  </defs>
  <polygon points="0,0 1200,0 1200,672 0,735" fill="url(#heroGrad)"/>
</svg>

<div class="abs site-name"><span class="mark"></span>BRIVO MOTORS</div>
<nav class="abs nav">
  <a class="active" href="#">Home</a><a href="#">Services</a><a href="#">About Us</a><a href="#">VIP</a><a href="#">Contact Us</a>
</nav>

<div class="abs hero-kicker">WELCOME TO BRIVO MOTORS</div>
<h1 class="abs hero-title">PRIVATE HIRE,<br>CHAUFFEUR AND<br>TAXI SERVICE</h1>
<div class="abs btn btn-yellow hero-btn">Book Now</div>
<div class="abs dots"><span class="arrow"></span><span style="background:#fff"></span><span></span><span></span><span></span><span class="arrow"></span></div>

<!-- Services -->
<h2 class="abs display section-title" style="top:768px">OUR SERVICES</h2>
<p class="abs section-lead" style="top:812px">malesuada iaculis ipsum dui aliquet felis at cursus magna nisl nec elit Praesent elementum elit at tellus nec ultricies sit amet porttitor mattis enim In</p>

<div class="abs service service-dark" style="left:190px;top:905px">
  <svg width="48" height="48" viewBox="0 0 48 48" fill="none" stroke="#fff" stroke-width="2"><rect x="3" y="3" width="42" height="42"/><path d="M24 10v28M12 26l12-6 12 6M18 36l6-3 6 3"/></svg>
  <h3>Allport<br>Transfers</h3>
  <p>Airport and Seaport transfers are a particular speciality of ours. We have in depth</p>
  <svg width="24" height="30" viewBox="0 0 24 30" style="margin-top:14px" fill="none" stroke="#fff" stroke-width="2"><path d="M12 2v25M4 19l8 8 8-8"/></svg>
</div>
<div class="abs service service-dark" style="left:721px;top:905px">
  <svg width="52" height="50" viewBox="0 0 52 50" fill="none" stroke="#fff" stroke-width="2"><path d="M14 44V8M14 8c-8 0-12 6-12 6M14 8c8 0 12 5 12 5M14 8c-2-4-8-5-8-5M14 8c3-4 9-4 9-4"/><circle cx="36" cy="34" r="7"/><path d="M4 46h46"/></svg>
  <h3>Holiday<br>Transfers</h3>
  <p>Why not start your holiday off stress free and allow us to take care of your outbound</p>
  <svg width="24" height="30" viewBox="0 0 24 30" style="margin-top:14px" fill="none" stroke="#fff" stroke-width="2"><path d="M12 2v25M4 19l8 8 8-8"/></svg>
</div>
<div class="abs service service-yellow" style="left:445px;top:905px">
  <svg width="92" height="40" viewBox="0 0 92 40" fill="none" stroke="#1b1b1b" stroke-width="3"><path d="M4 28v-8l14-4 12-10h28l16 10 12 2v10H4z"/><circle cx="24" cy="30" r="6" fill="#ffe100"/><circle cx="70" cy="30" r="6" fill="#ffe100"/><path d="M34 9v8M50 9v8"/></svg>
  <h3>Business to<br>Business Transfers</h3>
  <p>If its a stress free chauffeur service you need then look no further. A selection of vehicles</p>
  <svg width="24" height="30" viewBox="0 0 24 30" style="margin-top:10px" fill="none" stroke="#1b1b1b" stroke-width="2"><path d="M12 2v25M4 19l8 8 8-8"/></svg>
</div>

<!-- Always here band -->
<svg class="abs band" width="1200" height="600" viewBox="0 0 1200 600">
  <defs>
    <linearGradient id="bandGrad" x1="0" y1="0" x2="1" y2="0">
      <stop offset="0" stop-color="#ffe600"/>
      <stop offset="1" stop-color="#ffc400"/>
    </linearGradient>
  </defs>
  <polygon points="0,5 1200,90 1200,508 0,592" fill="url(#bandGrad)"/>
</svg>
<svg class="abs app-visual" viewBox="0 0 380 490" role="img" aria-label="Smartphone showing a taxi booking app map over orange rings">
  <defs>
    <radialGradient id="ringGrad" cx=".45" cy=".5" r=".5">
      <stop offset="0" stop-color="#f04a1a"/>
      <stop offset=".6" stop-color="#ff8a1a"/>
      <stop offset="1" stop-color="#ffd000" stop-opacity="0"/>
    </radialGradient>
  </defs>
  <circle cx="170" cy="240" r="175" fill="url(#ringGrad)"/>
  <rect x="80" y="30" width="200" height="430" rx="30" fill="#f3f3f3" transform="rotate(18 180 245)"/>
</svg>
<h2 class="abs display here-title">ALWAYS HERE FOR YOU</h2>
<div class="abs here-copy">
  <p>We provide airport transfers to and from all major UK airports, seaports, train station transfers and an executive business to business transfer service.</p>
  <p>Whether you have an individual or group transfer request, our company-owned fleet offers a choice of options to suit your needs, from luxury saloons and SUV's to 9-seat luxury transporters.</p>
</div>
<div class="abs btn btn-black here-btn">Learn More</div>

<!-- VIP -->
<h2 class="abs display vip-title">VIP</h2>
<div class="abs vip-copy">
  <p>malesuada iaculis ipsum dui aliquet felis at cursus magna nisl nec elit Praesent elementum elit at tellus nec ultricies sit amet porttitor mattis eni</p>
  <p>interdum nec interdum vel blandit sed nulla In ullamcorper est eget tempor cursus neq</p>
</div>
<div class="abs btn btn-yellow vip-btn">Learn More</div>
<div class="abs vip-accent"></div>
<svg class="abs vip-photo" viewBox="0 0 422 286" role="img" aria-label="VIP guest stepping out of a luxury car with cream leather interior">
  <defs>
    <linearGradient id="vipGrad" x1="0" y1="0" x2="1" y2="1">
      <stop offset="0" stop-color="#3a342d"/>
      <stop offset=".5" stop-color="#c9b796"/>
      <stop offset="1" stop-color="#2a2622"/>
    </linearGradient>
  </defs>
  <rect width="422" height="286" fill="url(#vipGrad)"/>
</svg>

<!-- Contact -->
<svg class="abs contact-bg" width="1200" height="566" viewBox="0 0 1200 566" role="img" aria-label="Dark background photo of a chauffeur at the wheel of a car">
  <defs>
    <linearGradient id="contactGrad" x1="0" y1="0" x2="1" y2="1">
      <stop offset="0" stop-color="#3a3a3a"/>
      <stop offset="1" stop-color="#4c4c4c"/>
    </linearGradient>
  </defs>
  <polygon points="0,3 1200,55 1200,566 0,566" fill="url(#contactGrad)"/>
  <polygon points="880,70 1200,55 1200,118" fill="#ffe100"/>
</svg>
<h2 class="abs contact-title">CONTACT US</h2>
<p class="abs contact-copy">Enim In massa libero interdum nec interdum vel blandit sed nulla In</p>
<div class="abs contact-line" style="top:2545px">
  <svg width="20" height="20" viewBox="0 0 24 24" fill="none" stroke="#fff" stroke-width="2"><path d="M5 3h4l2 5-3 2a12 12 0 0 0 6 6l2-3 5 2v4a2 2 0 0 1-2 2A18 18 0 0 1 3 5a2 2 0 0 1 2-2z"/></svg>
  07700 900214
</div>
<div class="abs contact-line" style="top:2580px">
  <svg width="20" height="20" viewBox="0 0 24 24" fill="none" stroke="#fff" stroke-width="2"><rect x="2" y="5" width="20" height="14"/><path d="M2 5l10 8 10-8"/></svg>
  info@brivomotors.co.uk
</div>
<div class="abs socials" style="left:172px;top:2620px"><span></span><span></span><span></span><span></span></div>

<form class="abs form-card">
  <h3 class="form-title">BOOK A RIDE WITH US</h3>
  <div class="field" style="left:36px;top:87px">First Name</div>
  <div class="field" style="left:276px;top:87px">Last Name</div>
  <div class="field" style="left:36px;top:131px">Email</div>
  <div class="field" style="left:276px;top:131px">Phone</div>
  <div class="field" style="left:36px;top:175px">
    <svg width="12" height="12" viewBox="0 0 12 12" fill="none" stroke="#8a8a8a"><rect x="1" y="2" width="10" height="9"/><path d="M1 5h10"/></svg>Date</div>
  <div class="field" style="left:276px;top:175px">
    <svg width="12" height="12" viewBox="0 0 12 12" fill="none" stroke="#8a8a8a"><circle cx="6" cy="6" r="5"/><path d="M6 3v3h2"/></svg>Time</div>
  <div class="btn btn-yellow form-btn">Book Now</div>
</form>

<!-- Footer -->
<nav class="abs footer-nav"><span>HOME</span><span>SERVICES</span><span>ABOUT US</span><span>VIP</span><span>CONTACT US</span></nav>
<p class="abs copyright">© 2018 Brivo Motors All right reserved</p>
<div class="abs socials dark" style="left:856px;top:2860px"><span></span><span></span><span></span><span></span></div>

</body>
</html>
```